Business Recognition Design

We need a design for a recognition to be given to business leaders in our community.
The recognition shall be made on a brass plaque on wood panel background (picture attached, please use it as a background), and all drawing must be in vectors and only one color (black).
It should also have a logo on the top and signature on the right bottom.
The text is enclosed in DOC file.
Updates

Reason: just to be able to find the best solution

Reason: None of the suggestion is good enough. Logo in general is too big in comparison with the rest of the plate.

Industry/Entity Type

Business

Requirements
Must have
• - standard Windows font (or possibility to install the same font on Windows), as the name on the recognition shall be printed in the same font
Nice to have
• - some graphic element (in curves) representing achievements in business
- should look great :)

```html
<!DOCTYPE html>
<html lang="de">
<head>
<meta charset="utf-8">
<title>Auszeichnung – Brelvanta</title>
<link rel="stylesheet" href="https://fonts.googleapis.com/css2?family=Arimo:wght@400;700&display=swap">
<style>
  :root {
    --wood-dark: #4a2a14;
    --wood-mid: #6e4122;
    --wood-light: #8a5530;
    --brass-deep: #b88a1c;
    --brass-mid: #d9b443;
    --brass-light: #f3dc7e;
    --brass-shine: #fbeaa0;
    --ink: #111111;
  }
  * { margin: 0; padding: 0; box-sizing: border-box; }
  html, body { width: 1200px; height: 922px; overflow: hidden; background: #ffffff; }
  .plaque {
    position: relative;
    width: 1200px; height: 922px;
    background: linear-gradient(135deg, var(--wood-light) 0%, var(--wood-mid) 35%, var(--wood-dark) 70%, var(--wood-mid) 100%);
    font-family: "Arimo", Arial, sans-serif;
    color: var(--ink);
  }
  .brass-plate {
    position: absolute;
    left: 47px; top: 47px; width: 1106px; height: 831px;
    background:
      linear-gradient(180deg, rgba(255,255,255,0.18) 0%, rgba(255,255,255,0) 40%),
      linear-gradient(115deg, var(--brass-deep) 0%, var(--brass-mid) 18%, var(--brass-light) 38%, var(--brass-shine) 50%, var(--brass-mid) 66%, var(--brass-light) 82%, var(--brass-deep) 100%);
    box-shadow: inset 0 0 0 2px rgba(120,85,10,0.55), inset 0 0 0 4px rgba(255,240,170,0.35), 0 2px 6px rgba(0,0,0,0.45);
  }
  .screw { position: absolute; width: 24px; height: 24px; }
  .line {
    position: absolute; left: 0; width: 1200px;
    text-align: center; line-height: 1; white-space: nowrap;
  }
  .brand-name { top: 179px; font-size: 92px; font-weight: 700; letter-spacing: -1px; }
  .brand-rule {
    position: absolute; left: 373px; top: 272px; width: 455px; height: 3px; background: var(--ink);
  }
  .title-large { font-size: 60px; font-weight: 400; letter-spacing: -0.5px; }
  .title-award { top: 298px; }
  .title-sub { top: 351px; font-size: 49px; font-weight: 400; }
  .title-role { top: 416px; }
  .title-country { top: 482px; font-size: 56px; }
  .recipient-prefix { top: 568px; font-size: 26px; }
  .recipient-name { top: 605px; font-size: 62px; font-weight: 700; }
  .citation { top: 702px; font-size: 24px; line-height: 34px; letter-spacing: 0.2px; }
  .footer-item { position: absolute; top: 804px; font-size: 24px; line-height: 1; letter-spacing: 0.5px; }
  .footer-place { left: 197px; }
  .footer-signatory { left: 788px; }
</style>
</head>
<body>
<main class="plaque">
  <div class="brass-plate"></div>

  <svg class="screw" style="left:77px;top:69px" viewBox="0 0 24 24" aria-hidden="true">
    <defs><radialGradient id="screwShade" cx="35%" cy="35%" r="65%"><stop offset="0" stop-color="#fff3b8"/><stop offset="0.5" stop-color="#d9b443"/><stop offset="1" stop-color="#6b4d0f"/></radialGradient></defs>
    <circle cx="12" cy="12" r="11" fill="url(#screwShade)"/>
  </svg>
  <svg class="screw" style="left:1110px;top:69px" viewBox="0 0 24 24" aria-hidden="true"><circle cx="12" cy="12" r="11" fill="url(#screwShade)"/></svg>
  <svg class="screw" style="left:77px;top:827px" viewBox="0 0 24 24" aria-hidden="true"><circle cx="12" cy="12" r="11" fill="url(#screwShade)"/></svg>
  <svg class="screw" style="left:1110px;top:827px" viewBox="0 0 24 24" aria-hidden="true"><circle cx="12" cy="12" r="11" fill="url(#screwShade)"/></svg>

  <div class="line brand-name">Brelvanta</div>
  <div class="brand-rule"></div>

  <div class="line title-large title-award">AUSZEICHNUNG</div>
  <div class="line title-sub">als herausragendster</div>
  <div class="line title-large title-role">UNTERNEHMER</div>
  <div class="line title-large title-country">Deutschlands 2013</div>

  <div class="line recipient-prefix">für Herrn Dipl.-Kfm.</div>
  <div class="line recipient-name">Max Muster</div>

  <p class="line citation">Unter der Leitung von Herr Dipl.-Kfm. Max Muster hat sich die FIRMA GmbH im Jahr<br>2013 unter den ersten 5% der größten deutschen Wirtschaftsunternehmen platziert.</p>

  <div class="footer-item footer-place">Gilching, 20. Juni 2013</div>
  <div class="footer-item footer-signatory">Lena Brandt</div>
</main>
</body>
</html>
```